LEARN Business Skills so you can Earn a good living

size of the poster is 8”x 10.75" plus 0.25" bleed.
Please leave 1 inch on the bottoum for footer
I want a design a poster that will attract people's attention.
I appreciate a creative ad however the ad should not take away from being able to clearly read the text.
-I also appreciate a simple creative ad that is not too busy.
-you can use graphics, vectors, or pictures of real people.
-however, if you use real people it should be a white male that is wearing a white shirt and look like a professional person.

Target Market(s)

Potential young business people

Industry/Entity Type

education

Requirements
Must have
• easy to read the text
Nice to have
• I would like a "creative" simple ad that is easy to be read
Should not have
• pictures of women

```html
<!DOCTYPE html>
<html lang="en">
<head>
<meta charset="utf-8">
<title>Learn It to Earn It – Business Enrichment Course</title>
<link rel="stylesheet" href="https://fonts.googleapis.com/css2?family=Montserrat:wght@300;400;700;800&family=Dancing+Script:wght@600&display=swap">
<style>
  :root {
    --page-bg: #8e8e8e;
    --ink-black: #0b0b0b;
    --ink-charcoal: #1a1a1a;
    --band-gray: #5c5c5c;
    --band-dark: #14110f;
    --paper-white: #ffffff;
    --text-light: #e4e4e4;
    --photo-light: #dcdcdc;
  }
  * { margin: 0; padding: 0; box-sizing: border-box; }
  html, body {
    width: 1200px;
    height: 1200px;
    overflow: hidden;
    background: var(--page-bg);
  }
  .poster {
    position: absolute;
    left: 207px;
    top: 80px;
    width: 787px;
    height: 1040px;
    background: var(--paper-white);
    overflow: hidden;
    font-family: "Montserrat", sans-serif;
  }
  .hero-band {
    position: absolute;
    left: 0; top: 0;
    width: 787px; height: 471px;
    background: radial-gradient(ellipse at 60% 40%, #262626 0%, var(--ink-charcoal) 45%, var(--ink-black) 100%);
  }
  .hero-photo {
    position: absolute;
    left: 205px; top: 60px;
    width: 375px; height: 411px;
    background: radial-gradient(ellipse 50% 55% at 60% 55%, var(--photo-light) 0%, rgba(190,190,190,0.8) 40%, rgba(90,90,90,0.3) 75%, rgba(30,30,30,0) 100%);
  }
  .info-band {
    position: absolute;
    left: 0; top: 471px;
    width: 787px; height: 476px;
    background: linear-gradient(180deg, var(--band-gray) 0%, #3e3e3e 45%, #262422 75%, var(--band-dark) 100%);
  }
  .footer-space {
    position: absolute;
    left: 0; top: 947px;
    width: 787px; height: 93px;
    background: var(--paper-white);
  }
  .headline {
    position: absolute;
    left: 0; top: 0;
    width: 787px; height: 1040px;
    overflow: visible;
  }
  .headline-word {
    font-family: "Montserrat", sans-serif;
    font-weight: 800;
    fill: var(--paper-white);
  }
  .headline-script {
    font-family: "Dancing Script", cursive;
    font-weight: 600;
    fill: var(--paper-white);
  }
  .course-title {
    position: absolute;
    right: 432px;
    top: 629px;
    text-align: right;
    color: var(--paper-white);
    font-weight: 700;
    font-size: 41px;
    line-height: 42px;
    letter-spacing: -0.5px;
    white-space: nowrap;
  }
  .course-tagline {
    position: absolute;
    right: 432px;
    top: 763px;
    text-align: right;
    color: var(--text-light);
    font-weight: 300;
    font-size: 13px;
    line-height: 18px;
    white-space: nowrap;
  }
  .benefits-intro {
    position: absolute;
    left: 425px;
    top: 637px;
    color: var(--text-light);
    font-weight: 400;
    font-size: 12.5px;
    white-space: nowrap;
  }
  .benefits {
    position: absolute;
    left: 425px;
    top: 655px;
    color: var(--paper-white);
    font-weight: 700;
    font-size: 24px;
    line-height: 36px;
    letter-spacing: -0.4px;
    white-space: nowrap;
  }
  .subject-list {
    position: absolute;
    left: 75px;
    top: 847px;
    color: var(--paper-white);
    font-weight: 700;
    font-size: 8.8px;
    line-height: 17.4px;
    text-transform: uppercase;
    white-space: nowrap;
  }
</style>
</head>
<body>
  <main class="poster">
    <div class="hero-band"></div>
    <div class="hero-photo" role="img" aria-label="Photo of a smiling young professional in a white shirt holding an open laptop"></div>
    <div class="info-band"></div>
    <div class="footer-space"></div>

    <svg class="headline" viewBox="0 0 787 1040" aria-label="Learn it to earn it">
      <defs>
        <filter id="lift" x="-5%" y="-20%" width="115%" height="160%">
          <feDropShadow dx="4" dy="10" stdDeviation="7" flood-color="#000" flood-opacity="0.55"/>
        </filter>
      </defs>
      <text class="headline-word" x="82" y="471" font-size="134" textLength="630" lengthAdjust="spacingAndGlyphs" filter="url(#lift)">LEARN IT</text>
      <text class="headline-script" x="76" y="589" font-size="86" textLength="84" lengthAdjust="spacingAndGlyphs">to</text>
      <text class="headline-word" x="163" y="590" font-size="134" textLength="549" lengthAdjust="spacingAndGlyphs" filter="url(#lift)">EARN IT</text>
    </svg>

    <h1 class="course-title">Business<br>Enrichment<br>Course</h1>
    <p class="course-tagline">A proven success of helping<br>people in their livelihoods</p>

    <p class="benefits-intro">Business skills that will help you:</p>
    <p class="benefits">Get a quality job -<br>start / grow your<br>business-Increase<br>your salary</p>

    <p class="subject-list">
      Business Admiistration – Small Business Management -<br>
      Finance - Investments - Computers- Accounting - Sales&nbsp; Marketing - Project Management Interviewing<br>
      Skills - Business Law -Negotiation – Public Speaking - Import/Export - Information Technoloy -<br>
      Distribution - Marketing -&nbsp;&nbsp; Ledgerly - Real Estate - Health Care-Management - Shopvale
    </p>
  </main>
</body>
</html>
```